Dog grooming business card
This is a business card for m dog grooming business like it say above.
In the priorities box below I will have the text that I want on the card.

Industry/Entity Type

Business

Colors

Designer to choose colors to be used in the design.

Requirements
Must have
• My logo and the insurance stamp must be on the card.

Text it must have :

Professional grooming services
Email: lunabrisk@mailvale.net
Text or call 1 705 318 6052
TWF certified/member
Pet first aid certified
Next appointment ___________________________________
Nice to have
• Greens to match my logo

```html
<!DOCTYPE html>
<html lang="en">
<head>
<meta charset="utf-8">
<title>Luna Brisk – Grooming Business Card</title>
<link href="https://fonts.googleapis.com/css2?family=Montserrat:wght@400;600;700&display=swap" rel="stylesheet">
<style>
  :root {
    --page-bg: #d9d9d9;
    --card-white: #ffffff;
    --olive: #a39a22;
    --olive-deep: #8c8514;
    --gold: #e6b914;
    --gold-light: #f1d24a;
    --text-olive: #9a8e17;
    --accent-violet: #8d6fd1;
    --fur: #e9d7bf;
  }
  * { box-sizing: border-box; margin: 0; padding: 0; }
  html, body { width: 1200px; height: 1000px; overflow: hidden; }
  body {
    background: var(--page-bg);
    font-family: "Montserrat", Arial, sans-serif;
    color: var(--text-olive);
  }
  .card {
    position: absolute;
    left: 250px;
    width: 700px;
    height: 400px;
    background: var(--card-white);
    overflow: hidden;
    box-shadow: 0 6px 18px rgba(0,0,0,0.18);
  }
  .card--back { top: 60px; }
  .card--front { top: 540px; }
  .card__shapes { position: absolute; inset: 0; width: 100%; height: 100%; }

  /* Back side */
  .insurer {
    position: absolute; left: 150px; top: 52px;
    text-align: left;
  }
  .insurer__eyebrow { font-size: 9px; letter-spacing: 3px; color: var(--olive); margin-left: 4px; }
  .insurer__name { font-size: 44px; font-weight: 700; color: var(--gold); line-height: 1.05; }
  .insurer__tagline { font-size: 10px; letter-spacing: 1.5px; color: var(--olive); margin-top: 4px; }

  .splash {
    position: absolute; left: 40px; top: 170px;
    width: 210px; height: 170px;
    border-radius: 48% 52% 45% 55%;
    background: radial-gradient(circle at 50% 55%, var(--gold) 0%, #d9a810 55%, rgba(230,185,20,0) 72%);
  }

  .contact {
    position: absolute; left: 385px; top: 150px;
    list-style: none;
    font-variant: small-caps;
    font-weight: 600;
    font-size: 15px;
    letter-spacing: 0.5px;
  }
  .contact__item { display: flex; align-items: center; gap: 9px; height: 29px; }
  .contact__icon { width: 13px; height: 13px; flex: none; }

  /* Front side */
  .client-name {
    position: absolute; left: 38px; top: 160px;
    display: flex; align-items: center; gap: 10px;
    font-size: 30px; font-weight: 700; color: var(--olive-deep);
  }
  .client-name__dot { width: 18px; height: 18px; border-radius: 50%; background: var(--gold); }
  .services-title {
    position: absolute; left: 250px; top: 128px; width: 330px;
    text-align: center;
    font-size: 20px; font-weight: 600; letter-spacing: 0.5px;
    color: var(--olive); line-height: 1.5;
  }
  .stamp {
    position: absolute; right: 34px; top: 72px;
    font-size: 22px; font-weight: 700; color: var(--olive-deep);
  }
  .mascot {
    position: absolute; right: 46px; top: 210px;
    width: 120px; height: 170px;
    border-radius: 40px 40px 18px 18px;
    background: linear-gradient(180deg, var(--fur) 0%, var(--fur) 45%, var(--accent-violet) 46%, #7256b8 100%);
  }
</style>
</head>
<body>

<section class="card card--back" aria-label="Card back">
  <svg class="card__shapes" viewBox="0 0 700 400" preserveAspectRatio="none" aria-hidden="true">
    <defs>
      <linearGradient id="back-gold" x1="0" y1="0" x2="0" y2="1">
        <stop offset="0" stop-color="#c9b21c"/>
        <stop offset="0.55" stop-color="#e6b914"/>
        <stop offset="1" stop-color="#b79f16"/>
      </linearGradient>
    </defs>
    <path d="M0 245 C 180 190, 330 300, 470 310 C 570 318, 640 320, 700 330 L700 400 L0 400 Z" fill="url(#back-gold)"/>
    <path d="M0 236 C 180 181, 330 291, 470 301 C 570 309, 640 311, 700 321" fill="none" stroke="#a39a22" stroke-width="1.5"/>
  </svg>

  <div class="splash" role="img" aria-label="Gold paint splash with paw prints"></div>

  <div class="insurer">
    <p class="insurer__eyebrow">PROTECTED BY</p>
    <p class="insurer__name">Coatguard</p>
    <p class="insurer__tagline">INSURANCE FOR PET CARE</p>
  </div>

  <ul class="contact">
    <li class="contact__item">
      <svg class="contact__icon" viewBox="0 0 12 12"><circle cx="6" cy="6" r="4.5" fill="#e6b914"/></svg>
      Professional grooming services
    </li>
    <li class="contact__item">
      <svg class="contact__icon" viewBox="0 0 12 12"><rect x="0.5" y="2.5" width="11" height="7" fill="#e6b914"/><path d="M0.5 2.5 L6 6.5 L11.5 2.5" fill="none" stroke="#fff" stroke-width="1"/></svg>
      lunabrisk@mailvale.net
    </li>
    <li class="contact__item">
      <svg class="contact__icon" viewBox="0 0 12 12"><path d="M2 1 L4.5 1 L5 4 L3.5 5 C4.3 6.8 5.2 7.7 7 8.5 L8 7 L11 7.5 L11 10 C6 11 1 6 2 1 Z" fill="#e6b914"/></svg>
      1 705 318 6052
    </li>
    <li class="contact__item">
      <svg class="contact__icon" viewBox="0 0 12 12"><path d="M1.5 6.5 L4.5 9.5 L10.5 2.5" fill="none" stroke="#e6b914" stroke-width="2.2"/></svg>
      TWF certified/member
    </li>
    <li class="contact__item">
      <svg class="contact__icon" viewBox="0 0 12 12"><path d="M1.5 6.5 L4.5 9.5 L10.5 2.5" fill="none" stroke="#e6b914" stroke-width="2.2"/></svg>
      Pet first aid certified
    </li>
  </ul>
</section>

<section class="card card--front" aria-label="Card front">
  <svg class="card__shapes" viewBox="0 0 700 400" preserveAspectRatio="none" aria-hidden="true">
    <defs>
      <linearGradient id="front-gold" x1="0" y1="0" x2="0" y2="1">
        <stop offset="0" stop-color="#c9b21c"/>
        <stop offset="0.5" stop-color="#e6b914"/>
        <stop offset="1" stop-color="#b0a018"/>
      </linearGradient>
    </defs>
    <rect x="0" y="0" width="700" height="48" fill="#a39a22"/>
    <line x1="0" y1="58" x2="700" y2="58" stroke="#a39a22" stroke-width="1.5"/>
    <path d="M0 270 C 140 225, 300 235, 450 275 C 560 305, 640 300, 700 285 L700 400 L0 400 Z" fill="url(#front-gold)"/>
    <path d="M0 262 C 140 217, 300 227, 450 267 C 560 297, 640 292, 700 277" fill="none" stroke="#a39a22" stroke-width="1.5"/>
  </svg>

  <div class="client-name">
    <span class="client-name__dot"></span>
    Luna Brisk
  </div>

  <p class="services-title">PROFESSIONAL GROOMING SERVICES</p>

  <p class="stamp">Coatguard</p>

  <div class="mascot" role="img" aria-label="Illustrated small dog wearing a violet grooming cape"></div>
</section>

</body>
</html>
```